Velvet Lantern rebranding my business with a new business card

I have my new logo and now I need a refresher on my business cards. I really want something fun and fresh. I like black background or anything to make the color pop.
Logo
Name: Velvet Lantern
Contact Info as stated below:
Mira Pellow
555-013-4762
Logo
Name: Velvet Lantern
Mira Pellow
555-013-4762
fb.me/VelvetLanternbyMira
Instagram: @VelvetLanternbyMira

Industry/Entity Type

Business

Contact Information for Business Card

double-sided. Logo on one side. Contact info on the other.

Requirements
Must have
• Logo
• Name: Velvet Lantern
• Contact Info as stated below:
• Mira Pellow
• 555-013-4762
• fb.me/VelvetLanternbyMira
• fb.me/VelvetLanternbyMira

```html
<!DOCTYPE html>
<html lang="en">
<head>
<meta charset="utf-8">
<title>Velvet Lantern – Business Card</title>
<link rel="stylesheet" href="https://fonts.googleapis.com/css2?family=Roboto:wght@400;500&family=Roboto+Condensed:wght@700&display=swap">
<style>
  :root {
    --backdrop: #e9e6e2;
    --card-white: #f7f7f6;
    --card-pink: #f0a6b4;
    --ring-pink: #f2a9b9;
    --ink-dark: #3b3536;
    --ink-mid: #55504f;
    --ink-soft: #5f5a5a;
  }
  * { margin: 0; padding: 0; box-sizing: border-box; }
  html, body {
    width: 1200px;
    height: 960px;
    overflow: hidden;
    background: var(--backdrop);
  }
  .stage {
    position: relative;
    width: 1200px;
    height: 960px;
  }
  .card {
    position: absolute;
    border-radius: 18px;
    box-shadow: 0 4px 12px rgba(0, 0, 0, 0.18);
    overflow: hidden;
  }

  /* Logo side */
  .card--front {
    left: 320px;
    top: 95px;
    width: 608px;
    height: 350px;
    background: var(--card-white);
  }
  .brand-seal {
    position: absolute;
    left: 193px;
    top: 71px;
    width: 204px;
    height: 204px;
    border-radius: 50%;
    border: 2px solid var(--ring-pink);
    background: #ffffff;
    display: flex;
    align-items: center;
    justify-content: center;
    text-align: center;
  }
  .brand-name {
    font-family: "Roboto Condensed", sans-serif;
    font-weight: 700;
    color: var(--ink-dark);
    text-transform: uppercase;
    line-height: 1.05;
  }
  .brand-seal .brand-name { font-size: 26px; letter-spacing: 0.04em; }
  .front-web {
    position: absolute;
    left: 0;
    right: 0;
    top: 316px;
    text-align: center;
    font-family: "Roboto", sans-serif;
    font-size: 15px;
    letter-spacing: 0.42em;
    color: var(--ink-mid);
  }

  /* Contact side */
  .card--back {
    left: 320px;
    top: 493px;
    width: 600px;
    height: 342px;
    background: var(--card-pink);
  }
  .holder-name {
    position: absolute;
    left: 32px;
    top: 26px;
    font-family: "Roboto Condensed", sans-serif;
    font-weight: 700;
    font-size: 22px;
    color: var(--ink-dark);
    text-transform: uppercase;
  }
  .contact-list {
    position: absolute;
    left: 33px;
    top: 61px;
    list-style: none;
    font-family: "Roboto", sans-serif;
    font-size: 14px;
    color: var(--ink-soft);
  }
  .contact-list li {
    display: flex;
    align-items: center;
    height: 19px;
  }
  .contact-icon {
    width: 12px;
    height: 12px;
    margin-right: 10px;
    flex: none;
  }
  .social-mark {
    width: 11px;
    height: 11px;
    margin-right: 11px;
    background: var(--ink-soft);
    border-radius: 1px;
    flex: none;
  }
  .back-brand {
    position: absolute;
    left: 300px;
    top: 150px;
    width: 280px;
    text-align: center;
  }
  .back-brand .brand-name { font-size: 46px; letter-spacing: 0.03em; }
</style>
</head>
<body>
<main class="stage">

  <section class="card card--front" aria-label="Business card, logo side">
    <div class="brand-seal">
      <span class="brand-name">Velvet<br>Lantern</span>
    </div>
    <p class="front-web">www.velvetlantern.com</p>
  </section>

  <section class="card card--back" aria-label="Business card, contact side">
    <h1 class="holder-name">Mira Pellow</h1>
    <ul class="contact-list">
      <li>
        <svg class="contact-icon" viewBox="0 0 24 24" aria-hidden="true">
          <path fill="#5f5a5a" d="M6.6 10.8a15.1 15.1 0 0 0 6.6 6.6l2.2-2.2c.3-.3.7-.4 1-.2 1.1.4 2.3.6 3.6.6.6 0 1 .4 1 1V20c0 .6-.4 1-1 1A17 17 0 0 1 3 4c0-.6.4-1 1-1h3.5c.6 0 1 .4 1 1 0 1.3.2 2.5.6 3.6.1.3 0 .7-.2 1z"/>
        </svg>
        555-013-4762
      </li>
      <li>
        <svg class="contact-icon" viewBox="0 0 24 24" aria-hidden="true">
          <circle cx="12" cy="12" r="10" fill="none" stroke="#5f5a5a" stroke-width="2.4"/>
          <path d="M2 12h20M12 2c3 3 3 17 0 20M12 2c-3 3-3 17 0 20" fill="none" stroke="#5f5a5a" stroke-width="1.8"/>
        </svg>
        www.velvetlantern.com
      </li>
      <li>
        <span class="social-mark" aria-hidden="true"></span>
        fb.me/VelvetLanternbyMira
      </li>
    </ul>
    <div class="back-brand">
      <span class="brand-name">Velvet<br>Lantern</span>
    </div>
  </section>

</main>
</body>
</html>
```